Thornvale Group needs a business card design

We need a new business card design using the logo recently selected in a logo competition on Pixel Bazaar. Our business is a consultancy specializing in aviation and energy and the winning business card design will promote an image of precision and professionalism with creativity.

Please use the logo with the name on the front of the card and use a complementary font. Make the back white with either the light grey or dark grey logo.

Target Market(s)

Senior finance and legal leaders at aviation and energy companies

Industry/Entity Type

Management Consulting

Contact Information for Business Card

Peter Castrell
President
Thornvale Group

www.thornvalegroup.example

(555) 204-6391
pc@thornvalegroup.example

Requirements
Must have
• Professional font that goes well with the logo font

```html
<!DOCTYPE html>
<html lang="en">
<head>
<meta charset="UTF-8">
<title>Thornvale Group – Business Card</title>
<link rel="stylesheet" href="https://fonts.googleapis.com/css2?family=Open+Sans:wght@400;600;700&display=swap">
<style>
  :root {
    --navy: #0f4a80;
    --ink: #1c1c1c;
    --muted: #3a3a3a;
    --paper: #ffffff;
    --tab-edge: #9aa3ad;
    --backdrop: #2e2926;
  }
  * { box-sizing: border-box; margin: 0; padding: 0; }
  html, body { width: 1200px; height: 844px; overflow: hidden; }
  body {
    background: var(--backdrop);
    font-family: "Open Sans", Arial, sans-serif;
    position: relative;
  }
  .card {
    position: absolute;
    top: 279px;
    width: 500px;
    height: 286px;
    background: var(--paper);
    overflow: hidden;
    box-shadow: 0 10px 24px rgba(0,0,0,0.45);
  }
  .card--contact { left: 70px; }
  .card--brand { left: 630px; }

  /* Contact side */
  .band { position: absolute; left: 0; right: 0; background: var(--navy); }
  .band--top { top: 0; height: 11px; }
  .band--bottom { bottom: 0; height: 14px; }

  .contact {
    position: absolute;
    left: 80px;
    right: 0;
    top: 38px;
    text-align: center;
  }
  .contact__name {
    display: inline-block;
    color: var(--navy);
    font-weight: 700;
    font-size: 17px;
    letter-spacing: 0.5px;
    padding: 0 4px 2px;
    border-bottom: 1.5px solid var(--navy);
  }
  .contact__title {
    color: var(--muted);
    font-size: 12px;
    margin-top: 2px;
  }
  .contact__details {
    margin-top: 30px;
    color: var(--muted);
    font-size: 12.5px;
    line-height: 1.55;
  }
  .services { margin-top: 28px; }
  .services__headline {
    color: var(--navy);
    font-weight: 700;
    font-size: 17px;
  }
  .services__sectors {
    color: var(--ink);
    font-weight: 600;
    font-size: 16px;
    margin-top: 2px;
    word-spacing: 2px;
  }

  /* Brand side */
  .tab {
    position: absolute;
    width: 16px;
    height: 34px;
    background: var(--navy);
  }
  .tab--right { right: 0; top: 44px; border-left: 3px solid var(--tab-edge); }
  .tab--left { left: 0; top: 178px; border-right: 3px solid var(--tab-edge); }

  .brand {
    position: absolute;
    inset: 0;
    display: flex;
    align-items: center;
    justify-content: center;
    gap: 12px;
  }
  .brand__square {
    width: 22px;
    height: 22px;
    background: var(--navy);
  }
  .brand__name {
    color: var(--navy);
    font-weight: 400;
    font-size: 34px;
    letter-spacing: 2px;
    text-transform: uppercase;
  }
</style>
</head>
<body>
  <section class="card card--contact" aria-label="Business card, contact side">
    <div class="band band--top"></div>
    <div class="contact">
      <div class="contact__name">PETER CASTRELL</div>
      <div class="contact__title">President</div>
      <div class="contact__details">
        <div class="contact__phone">(555) 204-6391</div>
        <div class="contact__email">pc@thornvalegroup.example</div>
      </div>
      <div class="services">
        <div class="services__headline">Finance and Strategy Consulting</div>
        <div class="services__sectors">Aviation | Manufacturing | Energy</div>
      </div>
    </div>
    <div class="band band--bottom"></div>
  </section>

  <section class="card card--brand" aria-label="Business card, brand side">
    <div class="tab tab--right"></div>
    <div class="tab tab--left"></div>
    <div class="brand">
      <span class="brand__square"></span>
      <span class="brand__name">Thornvale Group</span>
    </div>
  </section>
</body>
</html>
```